Vernac Law Business cards and stationary design project

We are looking for a stationary design for business cards (double sided), 8x10, 5x7, and legal and standard envelopes.

We would like the design to match the logo that we have already.
Color palate preferred is Teal, White, grey and any others that will look good for a professional law firm.

We would like this statement: "RELATIONSHIPS. RESPECT. RESULT" to be on the back of the business cards and maybe on the stationary if it looks good.

Please see link to website for more information: www.vernac-law.example

Target Market(s)

Potential clients that need Attorney services.

Industry/Entity Type

Law Firm

Contact Information for Business Card

We would like the front and back to be two different colors. Current business cards are teal front, grey back and are a vertical design. We are open to options with colors.

Font styles to use
Serif

Colors
33a6d7
33b8a4
b9b9b9
5c5c5c

Requirements
Must have
• Logo supplied needs to go on the card and stationary.
• Match website color palate, www.vernac-law.example
• Be professional and not too wordy.
• Criminal Law, Civil Litigation, Personal Injury, Restraining Orders need to be on the card.
Nice to have
• RELATIONSHIPS. RESPECT. RESULTS. on the back of the card.
Should not have
• Not be too busy/wordy or too flashy.

```html
<!DOCTYPE html>
<html lang="en">
<head>
<meta charset="utf-8">
<title>Vernac Law — Letterhead</title>
<link rel="stylesheet" href="https://fonts.googleapis.com/css2?family=Source+Sans+3:wght@400;700&display=swap">
<style>
  :root {
    --backdrop: #c9c9c9;
    --paper: #eeeeee;
    --teal: #1f7f8c;
    --ink: #5a5a5a;
    --ink-dark: #1e1e1e;
    --band: #0a0a0a;
    --band-text: #f2f2f2;
  }
  * { margin: 0; padding: 0; box-sizing: border-box; }
  html, body {
    width: 1200px; height: 1193px; overflow: hidden;
    background: var(--backdrop);
    font-family: "Source Sans 3", "Myriad Pro", sans-serif;
  }
  .letterhead {
    position: absolute; left: 177px; top: 112px;
    width: 768px; height: 994px;
    background: var(--paper);
    color: var(--ink);
  }
  .brand {
    position: absolute; left: 68px; top: 112px;
    display: flex; align-items: center; gap: 14px;
  }
  .brand-dot { width: 22px; height: 22px; border-radius: 50%; background: var(--teal); }
  .brand-name {
    font-size: 30px; font-weight: 400; color: var(--teal);
    letter-spacing: 2px; text-transform: uppercase;
  }
  .address-block {
    position: absolute; left: 69px; top: 298px;
    font-size: 13.5px; line-height: 1;
  }
  .address-block .date { margin-bottom: 12px; }
  .address-block .to { margin-bottom: 8px; }
  .address-block .line { font-size: 14.5px; margin-bottom: 5px; }
  .salutation { position: absolute; left: 69px; top: 423px; font-size: 13.5px; }
  .body-copy {
    position: absolute; left: 69px; top: 459px; width: 660px;
    font-size: 13.6px; line-height: 18.3px; white-space: nowrap;
  }
  .body-copy p { margin-bottom: 17.5px; }
  .signature-area {
    position: absolute; left: 69px; top: 786px;
    width: 132px; height: 50px;
    background: linear-gradient(90deg, #d9d9d9, #e4e4e4);
    border-radius: 3px;
  }
  .signatory {
    position: absolute; left: 72px; top: 843px;
    font-size: 15px; font-weight: 700; color: var(--ink-dark);
  }
  .contact-band {
    position: absolute; left: 0; top: 928px; width: 768px; height: 36px;
    background: var(--band);
    border-top: 2px solid var(--teal);
    border-bottom: 2px solid var(--teal);
    box-shadow: 0 -3px 0 var(--paper), 0 -4px 0 var(--teal), 0 3px 0 var(--paper), 0 4px 0 var(--teal);
    display: flex; align-items: center; justify-content: center;
    font-size: 12px; color: var(--band-text); white-space: nowrap;
  }
  .contact-item { display: flex; align-items: center; gap: 4px; }
  .contact-item svg { width: 10px; height: 10px; fill: var(--teal); }
  .divider { color: var(--teal); margin: 0 5px; }
  .tagline {
    position: absolute; left: 0; top: 969px; width: 768px;
    text-align: center; font-size: 12.5px; color: var(--ink);
  }
</style>
</head>
<body>
  <div class="letterhead">
    <div class="brand">
      <span class="brand-dot"></span>
      <span class="brand-name">Vernac Law</span>
    </div>

    <div class="address-block">
      <div class="date">December 24, 2015,</div>
      <div class="to">To: Dale Whitcombe</div>
      <div class="line">Northfield Group</div>
      <div class="line">City,State,Zip</div>
    </div>

    <div class="salutation">Dear Mr Whitcombe.</div>

    <div class="body-copy">
      <p>&nbsp; Lorem ipsum dolor sit amet, consectetur adipisicing elit, sed do eiusmod carte incididunt ut labore<br>et dolore magna aliqua. Ut enim ad minim veniam, quis &nbsp;exercitation ullamco laboris nisi ut aliquip<br>ex ea commodo consequat. review dolor in reprehenderit in voluptate .</p>
      <p>&nbsp; build voluptas sit aspernatur aut odit aut fugit, sed quia consequunture &nbsp;fugite ratione voluptatem<br>equi nesciunt. Neque porro quisquam est, qui dolor ipsum sit amet, consectetur, adipisci velit, sed<br>quia non numquam eius modilos iduim labore et dolore .</p>
      <p>&nbsp; Excepteur sint occaecat cupidatat non proident, sunt in culpa qui officia deser accusantium dolore<br>mque laudantium, totam rem aperiam, eaque ipsa quae an ratione voluptatem sequi nesciunt. Nequ<br>porro quisquam est, qui dolorem ie anim id est laborum. Sed ut perspiciatis unde omnis iste natus<br>error sit volupte accusantium doloremque laudantium, totam rem aperiam, eaque ipsa quae ab verit<br>atis et quasi architecto beatae vitae .</p>
      <p>&nbsp; Fuia voluptas sit aspernatur aut odit aut fugit, sed quia consequuntur magni &nbsp;ratione voluptatem seq<br>ui nesciunt. Neque porro quisquam est, qui dolorem eps sit amet, consectetur, adipisci velit, sed quia<br>non numquam eius modi tempora &nbsp;labore et dolore .</p>
    </div>

    <div class="signature-area" role="img" aria-label="Handwritten signature"></div>
    <div class="signatory">Ellen Marsh</div>

    <div class="contact-band">
      <span class="contact-item">
        <svg viewBox="0 0 10 10"><path d="M5 0a3.5 3.5 0 0 0-3.5 3.5C1.5 6 5 10 5 10s3.5-4 3.5-6.5A3.5 3.5 0 0 0 5 0zm0 5a1.5 1.5 0 1 1 0-3 1.5 1.5 0 0 1 0 3z"/></svg>
        418 Harbor View Rd. #200 , Coral Bay, CA 90000
      </span>
      <span class="divider">|</span>
      <span class="contact-item">
        <svg viewBox="0 0 10 10"><path d="M2 0.5 3.6 2.6 2.6 3.8c.7 1.5 2 2.8 3.6 3.6l1.2-1L9.5 8 8.3 9.5C4 9 1 6 .5 1.7z"/></svg>
        (555) 014-2286
      </span>
      <span class="divider">|</span>
      <span class="contact-item">
        <svg viewBox="0 0 10 10"><path d="M0 2h10v6H0zM0.6 2.4 5 5.6l4.4-3.2v.9L5 6.5.6 3.3z"/></svg>
        mara@vernac-law.example
      </span>
      <span class="divider">|</span>
      <span class="contact-item">
        <svg viewBox="0 0 10 10"><circle cx="5" cy="5" r="5"/></svg>
        www.vernac-law.example
      </span>
    </div>

    <div class="tagline">Clarity Counsel Commitment</div>
  </div>
</body>
</html>
```